Business card design for Brivo Engineering Tandem

We need a new business card design along with all the necessary to place an order. The company is Brivo Engineering Tandem and we recently updated our logo.

```html
<!DOCTYPE html>
<html lang="en">
<head>
<meta charset="utf-8">
<title>Brivo Engineering Tandem – Business Card</title>
<link rel="stylesheet" href="https://fonts.googleapis.com/css2?family=Montserrat:wght@400;500;600;700&display=swap">
<style>
  :root {
    --page-bg: #e9e7e6;
    --card-top: #f3eeec;
    --card-top-soft: #e8dedb;
    --steel-grey: #959595;
    --brand-yellow: #e2bc22;
    --logo-grey: #8f8f8f;
    --text-white: #ffffff;
  }
  * { margin: 0; padding: 0; box-sizing: border-box; }
  html, body {
    width: 1200px;
    height: 900px;
    overflow: hidden;
    background: var(--page-bg);
    font-family: "Montserrat", Arial, sans-serif;
  }
  .business-card {
    position: absolute;
    left: 150px;
    top: 172px;
    width: 900px;
    height: 556px;
    overflow: hidden;
    background: linear-gradient(160deg, var(--card-top) 0%, var(--card-top-soft) 100%);
    box-shadow: 0 10px 30px rgba(0, 0, 0, 0.18);
  }
  .card-waves {
    position: absolute;
    inset: 0;
    width: 100%;
    height: 100%;
  }
  .wave-accent { fill: var(--brand-yellow); }
  .wave-base { fill: var(--steel-grey); }
  .brand-lockup {
    position: absolute;
    left: 56px;
    top: 168px;
    display: flex;
    align-items: center;
    gap: 16px;
  }
  .brand-square {
    width: 30px;
    height: 30px;
    background: var(--brand-yellow);
  }
  .brand-name {
    font-size: 30px;
    font-weight: 600;
    letter-spacing: 1px;
    color: var(--logo-grey);
    text-transform: uppercase;
  }
  .holder {
    position: absolute;
    left: 54px;
    top: 387px;
    color: var(--text-white);
  }
  .holder-name {
    font-size: 36px;
    font-weight: 700;
    line-height: 1;
    color: var(--brand-yellow);
    text-transform: uppercase;
  }
  .holder-role {
    margin-top: 6px;
    font-size: 25px;
    font-weight: 400;
    line-height: 1.1;
  }
  .contact-list {
    position: absolute;
    right: 60px;
    top: 328px;
    list-style: none;
    color: var(--text-white);
    font-size: 24px;
    line-height: 33px;
  }
  .contact-item {
    display: flex;
    justify-content: flex-end;
    align-items: center;
    gap: 14px;
  }
  .contact-icon {
    width: 24px;
    height: 24px;
    fill: none;
    stroke: var(--brand-yellow);
    stroke-width: 2;
  }
  .contact-icon.filled { fill: var(--brand-yellow); stroke: none; }
  .postal-address {
    position: absolute;
    right: 62px;
    top: 444px;
    font-style: normal;
    text-align: right;
    color: var(--text-white);
    font-size: 24px;
    line-height: 33px;
  }
</style>
</head>
<body>
  <section class="business-card">
    <svg class="card-waves" viewBox="0 0 1090 673" preserveAspectRatio="none" aria-hidden="true">
      <path class="wave-accent" d="M0,335 C180,395 380,405 620,322 C780,270 900,262 1000,292 L1090,330 L1090,673 L0,673 Z"/>
      <path class="wave-base" d="M0,382 C200,422 390,402 630,332 C790,284 905,276 1005,302 L1090,340 L1090,673 L0,673 Z"/>
    </svg>

    <div class="brand-lockup">
      <span class="brand-square"></span>
      <span class="brand-name">Brivo Engineering Tandem</span>
    </div>

    <div class="holder">
      <h1 class="holder-name">Daniel Harlow</h1>
      <p class="holder-role">Managing Director</p>
    </div>

    <ul class="contact-list">
      <li class="contact-item">
        <span>044-555 018 274</span>
        <svg class="contact-icon" viewBox="0 0 24 24" aria-hidden="true">
          <path d="M6 3 L9 3 L10.5 7.5 L8.5 9 C9.5 11.5 12.5 14.5 15 15.5 L16.5 13.5 L21 15 L21 18 C21 19.5 19.5 21 18 21 C10 20.5 3.5 14 3 6 C3 4.5 4.5 3 6 3 Z"/>
          <path d="M14 3.5 A7 7 0 0 1 20.5 10"/>
        </svg>
      </li>
      <li class="contact-item">
        <span>hello@brivotandem.com</span>
        <svg class="contact-icon" viewBox="0 0 24 24" aria-hidden="true">
          <rect x="2" y="5" width="20" height="14" class="filled" style="fill:var(--brand-yellow);stroke:none"/>
          <path d="M2 5 L12 13 L22 5" style="stroke:var(--steel-grey)"/>
        </svg>
      </li>
      <li class="contact-item">
        <span>www.brivotandem.com</span>
        <svg class="contact-icon" viewBox="0 0 24 24" aria-hidden="true">
          <circle cx="12" cy="12" r="9.5"/>
          <ellipse cx="12" cy="12" rx="4" ry="9.5"/>
          <path d="M2.5 12 H21.5 M4 7 H20 M4 17 H20"/>
        </svg>
      </li>
    </ul>

    <address class="postal-address">
      18, Kestrel Works Lane<br>
      Northvale 40318, Eastmark
    </address>
  </section>
</body>
</html>
```